New travel store signage for Marlow Journeys to attract luxury travellers.

Hello,
We are looking to change the signage of our stores. The signage must include the following:
1. Marlow Journeys Logo (attached)
2. The text...The Travel & Cruise Experts
3. Brand Colours ( Fb0196, 412266, d41d84 and ffffff)
Please note the signage design must be central and only cover two thirds of the store front. We have also attached an image of one of our new stores which might be helpful when preparing a mock up.

We are looking for a quick turnaround on this, making a decision within 48 hours.

Target Market(s)

Retail

Industry/Entity Type

Travel Agency

Font styles to use
Other font styles liked:
• Radley

Colors
E54698
E96AAD
F1A4CE
F9D9EA
FCEFF6
6B429C
8869AF
B7A5CE
E3DAEB
F3F0F8

Requirements
Must have
• Hello, We are looking to change the signage of our stores. The signage must include the following: 1. Marlow Journeys Logo (attached) 2. The text...The Travel & Cruise Experts 3. Brand Colours ( Fb0196, 412266, d41d84 and ffffff) Please note the signage design must be central and only cover two thirds of the store front.
Should not have
• different colour or fonts. Gradient design.

```html
<!DOCTYPE html>
<html lang="en">
<head>
<meta charset="utf-8">
<title>Marlow Journeys – Store Signage</title>
<link rel="stylesheet" href="https://fonts.googleapis.com/css2?family=Radley&display=swap">
<style>
  :root {
    --brand-purple: #412266;
    --brand-pink: #fb0196;
    --brand-magenta: #d41d84;
    --brand-white: #ffffff;
    --canvas-bg: #a9a9a9;
  }
  * { margin: 0; padding: 0; box-sizing: border-box; }
  html, body {
    width: 1200px;
    height: 1117px;
    overflow: hidden;
  }
  body {
    background: var(--canvas-bg);
    display: flex;
    align-items: center;
    justify-content: center;
  }
  .store-sign {
    width: 1118px;
    height: 134px;
    display: flex;
    flex-direction: column;
    box-shadow: 0 4px 10px rgba(0, 0, 0, 0.35);
  }
  .sign-body {
    flex: 1;
    display: flex;
  }
  .brand-block {
    width: 380px;
    background: var(--brand-white);
    display: flex;
    align-items: center;
    justify-content: flex-end;
    gap: 10px;
    padding-right: 34px;
    padding-top: 10px;
  }
  .brand-mark {
    width: 12px;
    height: 12px;
    border-radius: 50%;
    background: var(--brand-magenta);
  }
  .brand-name {
    font-family: "Radley", serif;
    font-size: 22px;
    color: var(--brand-purple);
    white-space: nowrap;
  }
  .tagline-block {
    flex: 1;
    background: var(--brand-purple);
    display: flex;
    align-items: center;
    padding-left: 18px;
    padding-top: 6px;
  }
  .tagline {
    font-family: "Radley", serif;
    font-size: 44px;
    font-weight: 400;
    color: var(--brand-white);
    white-space: nowrap;
  }
  .accent-rule {
    height: 6px;
    background: var(--brand-pink);
  }
  .base-strip {
    height: 9px;
    background: var(--brand-purple);
    border-top: 3px solid var(--brand-white);
  }
</style>
</head>
<body>
  <div class="store-sign">
    <div class="sign-body">
      <div class="brand-block">
        <span class="brand-mark"></span>
        <span class="brand-name">Marlow Journeys</span>
      </div>
      <div class="tagline-block">
        <h1 class="tagline">The Travel &amp; Cruise Experts</h1>
      </div>
    </div>
    <div class="accent-rule"></div>
    <div class="base-strip"></div>
  </div>
</body>
</html>
```